Brindle Yard Care. The best in the biz

I run a lawn care service that offers full service mowing. 100% satisfaction guarantee. Fast, Friendly, quality service "I am your lawns best friend" I cut residential lawns. I offer a mow package that includes trimming, edging and clean up. Prices very from 20 dollars to 75. I want my logo to stand out. Free estimates

Target Market(s)

Home owners

Industry/Entity Type

Landscaping

Contact Information for Business Card

555-812-4473 tomvale48@quillmail.net Derek. Brindle Yard care

Colors
f37122
9bcb3c
cadf82

Requirements
Must have
• Company name.
• Phone number
• Email
• My services
• images
Nice to have
• A sun that is growing grass.
Should not have
• Incorrect information

```html
<!DOCTYPE html>
<html lang="en">
<head>
<meta charset="utf-8">
<title>Brindle Yard Care – Business Card</title>
<link href="https://fonts.googleapis.com/css2?family=Open+Sans:wght@400;600&display=swap" rel="stylesheet">
<style>
  :root {
    --backdrop: #3a3430;
    --card: #0b0b0b;
    --card-edge: #1a1a1a;
    --lime: #9bcb3c;
    --lime-soft: #cadf82;
    --orange: #f37122;
    --slate: #6b6b6b;
    --silver: #d4d4d4;
    --silver-dark: #8e8e8e;
    --ink-light: #f2f2f2;
  }
  * { box-sizing: border-box; margin: 0; padding: 0; }
  html, body {
    width: 1200px; height: 900px; overflow: hidden;
    background: var(--backdrop);
    font-family: "Open Sans", Arial, sans-serif;
  }
  .canvas {
    position: relative; width: 1200px; height: 900px;
    display: flex; align-items: center; justify-content: center; gap: 40px;
  }
  .card {
    width: 525px; height: 300px;
    background: var(--card);
    border: 1px solid var(--card-edge);
    box-shadow: 0 14px 30px rgba(0,0,0,.45);
    position: relative;
  }
  /* Contact side */
  .card--contact { display: flex; align-items: center; }
  .brand-block {
    width: 250px; height: 100%;
    display: flex; flex-direction: column; align-items: center; justify-content: center; gap: 14px;
  }
  .brand-disc {
    width: 120px; height: 120px; border-radius: 50%;
    background: var(--slate);
    border: 7px solid var(--lime);
  }
  .brand-name {
    color: var(--lime); font-size: 17px; font-weight: 600; letter-spacing: .3px;
  }
  .divider {
    width: 1px; height: 120px;
    background: linear-gradient(var(--lime), rgba(155,203,60,0));
  }
  .contact {
    padding-left: 26px; display: flex; flex-direction: column; gap: 6px;
    margin-top: -40px;
  }
  .contact__name { color: var(--lime); font-size: 17px; font-weight: 600; margin-bottom: 4px; }
  .contact__line { display: flex; align-items: center; gap: 10px; color: var(--ink-light); font-size: 14px; }
  .contact__icon { width: 12px; height: 12px; flex: none; }
  /* Brand side */
  .card--brand {
    display: flex; flex-direction: column; align-items: center; justify-content: center;
  }
  .brand-seal {
    width: 92px; height: 92px; border-radius: 50%;
    background: radial-gradient(circle at 35% 30%, #e6e6e6, var(--silver-dark));
    border: 3px solid var(--silver);
    margin-bottom: 14px;
  }
  .brand-title {
    color: var(--silver); font-size: 32px; font-weight: 400; letter-spacing: .5px;
    margin-bottom: 12px;
  }
  .tagline { color: var(--ink-light); font-size: 14.5px; line-height: 1.75; text-align: center; }
</style>
</head>
<body>
<main class="canvas">
  <section class="card card--contact">
    <div class="brand-block">
      <div class="brand-disc"></div>
      <div class="brand-name">Brindle Yard Care</div>
    </div>
    <div class="divider"></div>
    <div class="contact">
      <div class="contact__name">Derek</div>
      <div class="contact__line">
        <svg class="contact__icon" viewBox="0 0 12 12"><path fill="#9bcb3c" d="M2.5 0.8 4.3 3.1 3.4 4.4c.7 1.6 2.1 3 3.7 3.7l1.3-.9 2.3 1.8-1 1.9C5.4 10.8 1.2 6.6 1.1 2z"/></svg>
        <span>555-812-4473</span>
      </div>
      <div class="contact__line">
        <svg class="contact__icon" viewBox="0 0 12 12"><rect x="0.5" y="2" width="11" height="8" fill="#9bcb3c"/><path d="M0.5 2 6 6.5 11.5 2" fill="none" stroke="#0b0b0b" stroke-width="1.2"/></svg>
        <span>tomvale48@quillmail.net</span>
      </div>
    </div>
  </section>

  <section class="card card--brand">
    <div class="brand-seal"></div>
    <h1 class="brand-title">Brindle Yard Care</h1>
    <p class="tagline">100% satisfaction guarantee.<br>Fast, Friendly, Quality Service<br>I am your lawns best friend</p>
  </section>
</main>
</body>
</html>
```